Velmoria-Quillmesh Partial Redesign - Web App

Are you able to apply your creativity to an existing layout? I’m convinced that even just a few touches can make a big difference to add personality and professionalism to a website design, and I’m looking for someone able to use existing ideas and bring them to the next level while keeping inside some given constraints.
The actual job is to improve an existing design concept and to apply it creatively to a landing page, a simple home page, and an older web app (single page website).
To help you start with a clear picture of the current situation and of my requirements, I created a detailed brief with screenshots, live examples, and complete instructions. You can find it attached to this job.
My tastes are inclined towards clean and simple designs. For this project I'm not looking for dazzling novelty, but for very solid craftsmanship. Are the right man - or woman - for the job?
Updates
I wanted to thank everybody who participated in this project. I made a choice, but also other designs were interesting. Hope to work with you another time.
Target Market(s)
Our main target is social media marketers and startuppers
Look and feel
Each slider illustrates characteristics of the customer's brand and the style your logo design should communicate.

```html
<!DOCTYPE html>
<html lang="en">
<head>
<meta charset="utf-8">
<title>Velmoria – Hashtag Intelligence</title>
<link href="https://fonts.googleapis.com/css2?family=Open+Sans:ital,wght@0,400;0,600;0,700;0,800;1,400&display=swap" rel="stylesheet">
<style>
:root{
  --ink:#2b2b2b;
  --text:#444;
  --muted:#666;
  --dark:#3a3d42;
  --darker:#2e3034;
  --orange:#d9400f;
  --orange-dark:#b8330a;
  --blue:#2a78c8;
  --line:#e2e2e2;
  --row:#e9e9e9;
  --gold:#e8b21f;
  --white:#fff;
}
*{box-sizing:border-box;margin:0;padding:0}
html,body{width:1200px;height:2326px;overflow:hidden}
body{font-family:"Open Sans",Arial,sans-serif;color:var(--text);background:var(--white);position:relative}
.abs{position:absolute}

/* header */
.brand{left:150px;top:28px;display:flex;align-items:center;gap:16px}
.brand-dot{width:96px;height:60px;border-radius:50%;background:#ececec}
.brand-name{font-size:36px;font-weight:700;color:var(--ink);letter-spacing:-.5px}
.social-count{top:38px;display:flex;align-items:center;gap:6px}
.social-count .dot{width:28px;height:28px;border-radius:50%}
.social-count .num{background:#e6e6e6;border-radius:3px;font-size:12px;color:#333;padding:4px 10px}
.nav{left:0;top:110px;width:1200px;height:34px;background:var(--dark)}
.nav a{position:absolute;top:0;height:34px;line-height:34px;color:#fff;font-size:13px;font-weight:600;text-decoration:none;text-align:center;transform:translateX(-50%);padding:0 22px}
.nav a.active{background:var(--orange)}

/* hero */
.hero-title{left:158px;top:188px;font-size:27px;font-weight:800;color:var(--ink);letter-spacing:-.5px}
.hero-title em{font-style:normal;color:var(--orange)}
.hero-text{left:158px;top:236px;width:480px;font-size:13px;line-height:19px;color:#333}
.hero-list{left:166px;top:310px;list-style:none}
.hero-list li{font-size:12px;color:#444;height:31px;padding-left:20px;position:relative}
.hero-list li::before{content:"";position:absolute;left:0;top:5px;width:6px;height:6px;border-top:2px solid #333;border-right:2px solid #333;transform:rotate(45deg)}
.btn{display:inline-block;text-align:center;color:#fff;font-weight:700;border-radius:3px}
.btn-dark{background:var(--darker);font-size:12px}
.hero-btn{left:167px;top:436px;width:120px;height:32px;line-height:32px}
.dash{left:674px;top:240px;width:357px;height:245px;border:6px solid #eee;background:linear-gradient(#f4f4f4,#e3e3e3)}

.divider{left:70px;width:1060px;height:20px;background:radial-gradient(ellipse at top,rgba(0,0,0,.09),rgba(0,0,0,0) 70%)}

/* signup */
.step{display:flex;align-items:center;gap:14px;font-size:18px;color:var(--ink)}
.step-num{width:28px;height:26px;background:var(--dark);color:#fff;font-size:14px;font-weight:700;display:flex;align-items:center;justify-content:center;position:relative}
.step-num::after{content:"";position:absolute;right:-7px;top:6px;border-left:7px solid var(--dark);border-top:7px solid transparent;border-bottom:7px solid transparent}
.form-row{left:175px;width:400px;height:31px;display:flex;align-items:center}
.form-row label{width:104px;font-size:11px;color:#333}
.form-row span{flex:1;height:31px;border:1px solid #ddd;border-radius:3px;background:#fff;box-shadow:inset 0 1px 2px rgba(0,0,0,.06)}
.submit{left:282px;top:828px;width:98px;height:32px;line-height:32px}
.vrule{left:606px;top:573px;width:1px;height:287px;background:var(--line)}
.price-head{left:656px;top:624px;font-size:22px;color:#444}
.price-text{left:656px;top:659px;width:252px;font-size:12px;line-height:19px;color:#555}
.seal{left:922px;top:620px;width:120px;height:120px;border-radius:50%;background:radial-gradient(circle,#f6cc4a 45%,var(--gold) 46%,#c9920f 100%)}
.btn-orange{background:var(--orange);font-size:15px;box-shadow:inset 0 -2px 0 var(--orange-dark)}
.buy1{left:654px;top:818px;width:121px;height:42px;line-height:42px}

/* compare */
.section-title{left:0;top:922px;width:1200px;text-align:center;font-size:29px;color:var(--orange);font-weight:400}
.hr{height:1px;background:var(--line)}
.col-title{font-size:17px;color:#333}
.plans{left:152px;top:1035px;width:333px;height:131px;background:var(--dark);border-radius:3px;display:flex;overflow:hidden}
.plan{flex:1;text-align:center;color:#fff}
.plan h4{font-size:12px;font-weight:700;height:32px;line-height:32px;background:var(--darker)}
.plan .amt{font-size:32px;font-weight:600;margin-top:14px;line-height:36px}
.plan .per{font-size:11px;font-weight:600}
.plan.alt{background:#55585d}
.plan.alt h4{background:#3f4247}
.features{left:150px;top:1198px;width:572px;border-collapse:collapse;font-size:13px;color:#333}
.features td{height:45px}
.features tr:nth-child(odd){background:var(--row)}
.features td:first-child{padding-left:31px;width:300px}
.features td:nth-child(2){width:160px;padding-left:16px}
.features td:nth-child(3){padding-left:0}
.note{left:158px;top:1526px;width:370px;font-size:11px;line-height:17px;color:var(--blue)}
.btn-blue{background:var(--blue);font-size:13px;box-shadow:inset 0 -2px 0 #1e5ea0}
.buy2{left:581px;top:1524px;width:82px;height:35px;line-height:35px}
.testimonials{left:761px;top:1040px;width:287px}
.quote{padding:11px 0 14px;border-bottom:1px solid var(--line)}
.quote p{font-size:11px;font-style:italic;line-height:19px;color:#555}
.quote b{display:block;font-size:11px;color:#222;margin-top:10px}

/* gallery */
.shot{width:160px;height:157px;border:1px solid #ddd;padding:5px;background:#fff}
.shot div,.video div{width:100%;height:100%;background:linear-gradient(#f2f1ea,#e3e1d6)}
.video{left:764px;width:282px;height:164px;border:1px solid #ddd;padding:5px;background:#fff}

/* footer */
.footer{left:0;top:2282px;width:1200px;height:44px;background:var(--dark);color:#ccc;font-size:11px}
.footer .copy{position:absolute;left:143px;top:14px}
.footer .icons{position:absolute;left:561px;top:13px;display:flex;gap:3px}
.footer .icons i{width:18px;height:18px;border-radius:2px;display:block}
.footer .legal{position:absolute;left:949px;top:14px}
.footer .code{position:absolute;left:1162px;top:12px;color:#fff}
</style>
</head>
<body>

<header>
  <div class="abs brand"><span class="brand-dot"></span><span class="brand-name">Velmoria</span></div>
  <div class="abs social-count" style="left:778px"><span class="dot" style="background:#3aaee3"></span><span class="num">336,365</span></div>
  <div class="abs social-count" style="left:908px"><span class="dot" style="background:#3b5998"></span><span class="num">336,365</span></div>
  <nav class="abs nav">
    <a style="left:198px">About</a>
    <a style="left:305px">Summary</a>
    <a style="left:418px">Time line</a>
    <a style="left:541px">Influencers</a>
    <a class="active" style="left:656px;width:96px">Hash tag</a>
    <a style="left:752px">Blog</a>
  </nav>
</header>

<section class="hero">
  <h1 class="abs hero-title">Start getting detailed intelligence for <em>#your hashtag now!</em></h1>
  <p class="abs hero-text">Lorem ipsum dolor sit amet, consectetuer adipiscing elit. Nam cursus. Morbi ut mi. Nullam enim leo.Lorem ipsum dolor sit amet, consectetuer adipiscing elit. Nam cursus. Morbi ut mi. Nullam enim leo.</p>
  <ul class="abs hero-list">
    <li>Discover and track trends as they develop</li>
    <li>Learn everything about up to 50 top influencers</li>
    <li>Evaluate and compare your own influencers</li>
    <li>Read the actual tweets where influence is exercised</li>
  </ul>
  <span class="abs btn btn-dark hero-btn">LEARN MORE</span>
  <div class="abs dash" role="img" aria-label="Trend analysis dashboard with statistics and two trend gauges and a play button"></div>
</section>

<div class="abs divider" style="top:522px"></div>

<section class="signup">
  <div class="abs step" style="left:174px;top:567px"><span class="step-num">1</span>Create Your Account</div>
  <div class="abs form-row" style="top:625px"><label>Email:</label><span></span></div>
  <div class="abs form-row" style="top:664px"><label>First Name:</label><span></span></div>
  <div class="abs form-row" style="top:703px"><label>Last Name:</label><span></span></div>
  <div class="abs form-row" style="top:741px"><label>Password:</label><span></span></div>
  <div class="abs form-row" style="top:780px"><label>Repeat Password:</label><span></span></div>
  <span class="abs btn btn-dark submit">SUBMIT NOW</span>

  <div class="abs vrule"></div>

  <div class="abs step" style="left:648px;top:567px"><span class="step-num">2</span>Checkout Only 5$ Per Month</div>
  <h2 class="abs price-head" style="font-weight:400">Only Per Month 5$</h2>
  <p class="abs price-text">Lorem ipsum dolor sit amet, consectetuer adipiscing elit. Nam cursus. Morbi ut mi. Nullam enim leo, egestas id, condimentum at, laoreet mattis, massa. Lorem ipsum dolor sit amet, consectetuer adipiscing elit. Nam cursus. Morbi ut mi. Nullam enim leo, egestas id, condimentum at, laoreet mattis, massa.</p>
  <div class="abs seal"></div>
  <span class="abs btn btn-orange buy1">Buy Now</span>
</section>

<div class="abs divider" style="top:888px"></div>

<section class="compare">
  <h2 class="abs section-title">Want to learn more before buying?</h2>
  <div class="abs hr" style="left:150px;top:976px;width:900px"></div>

  <h3 class="abs col-title" style="left:150px;top:990px;font-weight:400">Compare Features</h3>
  <div class="abs hr" style="left:150px;top:1023px;width:599px;background:#d8d8d8"></div>
  <div class="abs plans">
    <div class="plan"><h4>quillmesh.me</h4><div class="amt">$0</div><div class="per">Per Month</div></div>
    <div class="plan alt"><h4>Hashtag Intelligence</h4><div class="amt">$5</div><div class="per">Per Month</div></div>
  </div>
  <table class="abs features">
    <tr><td>Basic Hashtag Data</td><td>Yes</td><td>Yes</td></tr>
    <tr><td>100% Sampling</td><td>No *</td><td>Yes</td></tr>
    <tr><td>Trend Analysis</td><td>No</td><td>Yes</td></tr>
    <tr><td>Up To 50 Top Influencers</td><td>No</td><td>Yes</td></tr>
    <tr><td>Track Your Own Influencers</td><td>No</td><td>Yes</td></tr>
    <tr><td>Up To 50 Related Hashtags</td><td>No</td><td>Yes</td></tr>
    <tr><td>Read Actual Influential Tweets</td><td>No</td><td>Yes</td></tr>
  </table>
  <p class="abs note">Prices are per active hashtag, per month. You can cancel your account at any time. Sales taxes not included.</p>
  <span class="abs btn btn-blue buy2">Buy Now</span>
  <div class="abs hr" style="left:150px;top:1573px;width:530px"></div>

  <h3 class="abs col-title" style="left:761px;top:990px;font-weight:400">What people are saying</h3>
  <div class="abs hr" style="left:761px;top:1023px;width:287px;background:#d8d8d8"></div>
  <div class="abs testimonials">
    <div class="quote"><p>Mail sent through [Postwell] has the highest delivery rate of any competitor we have tested.</p><b>Daniel Korvath</b></div>
    <div class="quote"><p>I just successfully put a signup web form on my website, thanks to the complete and easy descriptive video and written instructions. Excellent! If a middle-aged geologist with a graduate degree in finance and little to no web savvy can do it, then anyone can.</p><b>Tom Harlow MBA P.Geo</b></div>
    <div class="quote"><p>Your service is terrific! I've never dealt with an organization that responded so thoroughly, quickly, and patiently.</p><b>Gavin Trelford Pike</b></div>
    <div class="quote"><p>Mail sent through [Postwell] has the highest delivery rate of any competitor we have tested.</p><b>Daniel Korvath</b></div>
    <div class="quote" style="border:0"><p>I just successfully put a signup web form on my website, thanks to the complete and easy descriptive video and written instructions. Excellent! If a middle-aged geologist with a graduate degree in finance and little to no web savvy can do it, then anyone can. Thanks!</p><b>Tom Harlow MBA P.Geo.</b></div>
  </div>
</section>

<div class="abs divider" style="top:1594px"></div>

<section class="gallery">
  <h3 class="abs col-title" style="left:150px;top:1633px;font-weight:400">Screenshots Gallery</h3>
  <div class="abs hr" style="left:150px;top:1666px;width:599px;background:#d8d8d8"></div>
  <div class="abs shot" style="left:152px;top:1696px"><div role="img" aria-label="Screenshot of a pie chart"></div></div>
  <div class="abs shot" style="left:363px;top:1696px"><div role="img" aria-label="Screenshot of the campaign dashboard with a trend gauge"></div></div>
  <div class="abs shot" style="left:570px;top:1696px"><div role="img" aria-label="Screenshot of a profile table"></div></div>
  <div class="abs shot" style="left:152px;top:1872px"><div role="img" aria-label="Screenshot of a timeline line chart with tweets"></div></div>
  <div class="abs shot" style="left:363px;top:1872px"><div role="img" aria-label="Screenshot of a pie chart"></div></div>
  <div class="abs shot" style="left:570px;top:1872px"><div role="img" aria-label="Screenshot of the campaign dashboard with a trend gauge"></div></div>
  <div class="abs shot" style="left:152px;top:2046px"><div role="img" aria-label="Screenshot of a profile table"></div></div>
  <div class="abs shot" style="left:363px;top:2046px"><div role="img" aria-label="Screenshot of a timeline line chart with tweets"></div></div>
  <div class="abs shot" style="left:570px;top:2046px"><div role="img" aria-label="Screenshot of the campaign dashboard with a trend gauge"></div></div>

  <h3 class="abs col-title" style="left:763px;top:1633px;font-weight:400">More Videos</h3>
  <div class="abs hr" style="left:763px;top:1666px;width:285px;background:#d8d8d8"></div>
  <div class="abs video" style="top:1694px"><div role="img" aria-label="Video thumbnail with two trend gauges and a play button"></div></div>
  <div class="abs video" style="top:1868px"><div role="img" aria-label="Video thumbnail with two trend gauges and a play button"></div></div>
  <div class="abs video" style="top:2038px"><div role="img" aria-label="Video thumbnail with two trend gauges and a play button"></div></div>
</section>

<div class="abs divider" style="top:2240px"></div>

<footer class="abs footer">
  <span class="copy">© 2012. Velmoria Ltd. All Rights Reserved.</span>
  <span class="icons"><i style="background:#3b5998"></i><i style="background:#3aaee3"></i><i style="background:#1f7bc4"></i><i style="background:#c4402f"></i><i style="background:#e8822a"></i></span>
  <span class="legal">Privacy Policy | T&amp;C</span>
  <span class="code">C2</span>
</footer>

</body>
</html>
```